Plotvista Caribbean

We need a vibrant, user friendly and exciting website for our land search company called "plotVista" This application will help individuals locate and or list lots for sale within the Caribbean. We will offer a small cash back incentive to buyers that purchase land from our site, and we will charge a 1%-2% success fee to our sellers once a successful transaction is made. We would like to become a match making site, matching buyers and sellers on our platform. We will also include a service directory and marketing advertisement spot for other service providers for a fee. We would like to see a webdesign incorporating Caribbean colors (blue, green and yellow) with very modern clean lines, very picturesque and easy to use.

Industry/Entity Type

Real Estate

Coding

Coded - Design and coding required

Number of Pages Required

5+ page

Font styles to use
Sans Serif

Colors
ffffff
85acd3
b768aa
dbdbdb

Requirements
Nice to have
• Scenic photos of the ocean and beautiful landscape

```html
<!DOCTYPE html>
<html lang="en">
<head>
<meta charset="utf-8">
<title>plotVista – Land Lovers</title>
<link rel="stylesheet" href="https://fonts.googleapis.com/css2?family=Oswald:wght@400;500&family=Open+Sans:wght@400;600;700&display=swap">
<style>
:root{
  --white:#ffffff;
  --blue:#85acd3;
  --purple:#b768aa;
  --grey:#dbdbdb;
  --lavender:#e9ebf7;
  --dark:#2a2d35;
  --ink:#333840;
  --muted:#6b6f78;
}
*{box-sizing:border-box;margin:0;padding:0}
html,body{width:1200px;height:3564px;overflow:hidden}
body{position:relative;background:var(--lavender);font-family:"Open Sans",sans-serif;color:var(--ink)}
.abs{position:absolute}
.heading{font-family:"Oswald",sans-serif;font-weight:400;text-transform:uppercase;letter-spacing:1px;line-height:1.2}

/* hero */
.hero{left:0;top:0;width:1200px;height:551px;background:linear-gradient(180deg,#6f8fae 0%,#8fb1c9 22%,#3f7a5a 38%,#2aa6b8 55%,#17b5b0 70%,#3d7a48 100%)}
.nav{left:0;top:0;width:1200px;height:102px;background:rgba(20,24,32,.78)}
.brand{left:86px;top:28px;height:46px;display:flex;align-items:center;gap:12px;color:var(--white);font-family:"Oswald",sans-serif;font-size:38px;font-weight:500;letter-spacing:1px}
.brand .mark{width:34px;height:34px;background:var(--purple)}
.menu{top:28px;height:44px;font-family:"Open Sans",sans-serif;font-size:15px;font-weight:600;color:var(--white);display:flex;align-items:center;justify-content:center;text-transform:uppercase}
.menu.active{background:var(--purple)}
.hero-title{left:86px;top:202px;font-size:46px;line-height:54px;color:var(--white);font-family:"Oswald",sans-serif;font-weight:500;letter-spacing:1px}
.hero-text{left:86px;top:264px;width:470px;font-size:14px;line-height:17px;font-style:italic;color:var(--white);font-weight:600}
.btn-blue{background:var(--blue);color:var(--white);font-size:14px;font-weight:600;display:flex;align-items:center;justify-content:center}
.arrow{top:336px;width:26px;height:40px;background:rgba(0,0,0,.35)}

/* search */
.search{left:86px;top:440px;width:1028px;height:237px;background:var(--grey)}
.search-title{left:0;width:100%;top:22px;text-align:center;font-size:25px;color:#444}
.search-sub{left:0;width:100%;top:56px;text-align:center;font-size:17px;color:#555}
.field{top:101px;height:48px;background:var(--white);font-size:14px;color:#777;display:flex;align-items:center;justify-content:space-between;padding:0 24px 0 40px}
.label{top:180px;font-size:15px;color:#555}
.track{top:189px;height:3px;background:var(--white)}
.knob{width:22px;height:22px;border-radius:50%;border:3px solid var(--blue);background:var(--white);top:-10px}
.btn-search{left:769px;top:163px;width:235px;height:50px;background:var(--purple);color:var(--white);font-size:16px;display:flex;align-items:center;justify-content:center;gap:18px}

/* properties */
.section-title{left:0;width:1200px;text-align:center;font-size:27px;color:var(--ink)}
.rule{height:3px;background:var(--blue);width:100px;left:550px}
.card{width:332px;height:371px;background:var(--white)}
.card-name{left:18px;top:22px;font-family:"Oswald",sans-serif;font-size:19px;letter-spacing:.5px;color:var(--ink);text-transform:uppercase}
.card-photo{left:0;top:81px;width:332px;height:209px}
.tag{right:14px;top:62px;width:96px;height:36px;background:#1d1f24;color:var(--white);font-family:"Oswald",sans-serif;font-size:15px;display:flex;align-items:center;justify-content:center}
.btn-dark{left:104px;top:314px;width:124px;height:33px;background:#1d1f24;color:var(--white);font-size:12px;font-weight:700;display:flex;align-items:center;justify-content:center}

/* about */
.about{left:0;top:1663px;width:1200px;height:400px;background:var(--white)}
.about-title{left:83px;top:62px;font-size:27px}
.about-rule{left:83px;top:105px;width:82px;height:3px;background:var(--blue)}
.about-text{left:83px;top:126px;width:640px;font-size:13px;line-height:20px;color:#555}
.about-photo{left:760px;top:0;width:230px;height:400px;background:linear-gradient(180deg,#f3f3f3 0%,#e6e6e6 40%,#7a5443 60%,#2b3146 100%)}

/* team */
.quote{padding:40px 16px 14px;font-size:12px;line-height:18px;color:var(--white)}
.quote-icon{width:32px;height:32px;border-radius:50%;background:var(--white);top:-14px;left:14px;display:flex;align-items:center;justify-content:center}
.avatar{border-radius:50%;border:4px solid var(--white);background:linear-gradient(180deg,#c9d6dc,#8e9ea8)}
.member{font-size:12px;color:#888;text-align:center}

/* services */
.services{left:0;top:2692px;width:1200px;height:487px;background:var(--blue)}
.svc-label{top:153px;width:193px;text-align:center;color:var(--white);font-size:16px}
.svc-photo{top:176px;width:193px;height:195px}
.dot{top:417px;width:12px;height:12px;border-radius:50%;background:var(--white)}

/* signup */
.signup{left:0;top:3179px;width:1200px;height:114px;background:var(--purple)}
.signup-title{left:86px;top:28px;font-size:33px;line-height:40px;color:var(--white);font-family:"Oswald",sans-serif;font-weight:500}
.signup-sub{left:86px;top:71px;font-size:11px;color:var(--white)}
.email{left:566px;top:34px;width:366px;height:42px;background:var(--white);font-size:13px;color:#666;display:flex;align-items:center;padding-left:18px}
.submit{left:944px;top:34px;width:127px;height:42px;font-size:15px}

/* footer */
.footer{left:0;top:3293px;width:1200px;height:271px;background:var(--dark);color:var(--white)}
.foot-brand{left:86px;top:92px;font-size:44px}
.reach{left:542px;top:40px;font-family:"Oswald",sans-serif;font-size:22px;letter-spacing:1px}
.contact{top:104px;font-size:13px;display:flex;align-items:center;gap:8px}
.social{top:148px;width:16px;height:16px;border-radius:50%;background:var(--white)}
.foot-line{left:0;top:207px;width:1200px;height:1px;background:#4a4e58}
.foot-links{left:86px;top:232px;font-size:12px;color:#cfd2d8}
.copy{right:86px;top:232px;font-size:12px;color:#cfd2d8}
</style>
</head>
<body>

<div class="abs hero" role="img" aria-label="Aerial view of a turquoise Caribbean bay with green hills"></div>
<header class="abs nav">
  <div class="abs brand"><span class="mark"></span>PLOTVISTA</div>
  <div class="abs menu active" style="left:501px;width:80px">Home</div>
  <div class="abs menu" style="left:597px;width:50px">Buy</div>
  <div class="abs menu" style="left:668px;width:54px">Sell</div>
  <div class="abs menu" style="left:752px;width:100px">Services</div>
  <div class="abs menu" style="left:858px;width:70px">Deals</div>
  <div class="abs menu" style="left:940px;width:82px">Agents</div>
  <div class="abs menu" style="left:1032px;width:120px">Contact Us</div>
</header>
<h1 class="abs hero-title">WELCOME TO PLOTVISTA</h1>
<p class="abs hero-text">We will offer a small cash back incentive to buyers that purchase land from our site, and we will charge a 1%-2% success fee to our sellers once a successful transaction is made.</p>
<div class="abs btn-blue" style="left:86px;top:337px;width:104px;height:36px">READ MORE</div>
<div class="abs arrow" style="left:0"><svg width="26" height="40"><path d="M16 12 L9 20 L16 28" stroke="#fff" stroke-width="3" fill="none"/></svg></div>
<div class="abs arrow" style="right:0"><svg width="26" height="40"><path d="M10 12 L17 20 L10 28" stroke="#fff" stroke-width="3" fill="none"/></svg></div>

<section class="abs search">
  <div class="abs heading search-title">Land Lovers</div>
  <div class="abs search-sub">Matching Buyers and Sellers</div>
  <div class="abs field" style="left:23px;width:309px">List of Caribbean
    <svg width="12" height="16"><path d="M6 1a5 5 0 0 1 5 5c0 4-5 9-5 9S1 10 1 6a5 5 0 0 1 5-5z" fill="#666"/><circle cx="6" cy="6" r="2" fill="#fff"/></svg></div>
  <div class="abs field" style="left:354px;width:316px">Cash Buyer
    <svg width="12" height="8"><path d="M1 1l5 5 5-5" stroke="#666" stroke-width="1.5" fill="none"/></svg></div>
  <div class="abs field" style="left:684px;width:318px">Mountain
    <svg width="12" height="8"><path d="M1 1l5 5 5-5" stroke="#666" stroke-width="1.5" fill="none"/></svg></div>
  <div class="abs label" style="left:35px">Price</div>
  <div class="abs track" style="left:140px;width:225px"><div class="abs knob" style="left:42px"></div></div>
  <div class="abs label" style="left:399px">Size</div>
  <div class="abs track" style="left:437px;width:247px"><div class="abs knob" style="left:55px"></div></div>
  <div class="abs btn-search">Search
    <svg width="16" height="16"><circle cx="6.5" cy="6.5" r="5" stroke="#fff" stroke-width="2" fill="none"/><path d="M10 10l5 5" stroke="#fff" stroke-width="2"/></svg></div>
</section>

<h2 class="abs heading section-title" style="top:740px">Latest Properties</h2>
<div class="abs rule" style="top:787px"></div>

<article class="abs card" style="left:88px;top:829px"><div class="abs card-name">British Virgin Islands BVI</div><div class="abs card-photo" role="img" aria-label="Couple sitting on a white beach under palms" style="background:linear-gradient(180deg,#4d9be0,#bfe0f4 55%,#efe6d2)"></div><div class="abs tag">FOR SALE</div><div class="abs btn-dark">MORE DETAILS</div></article>
<article class="abs card" style="left:434px;top:829px"><div class="abs card-name">United States Virgin Islands USVI</div><div class="abs card-photo" role="img" aria-label="Thatched beach huts by shallow water" style="background:linear-gradient(180deg,#dfe7ec,#a48b62 45%,#5f8a7a)"></div><div class="abs tag">FOR SALE</div><div class="abs btn-dark">MORE DETAILS</div></article>
<article class="abs card" style="left:780px;top:829px"><div class="abs card-name">Antigua &amp; Barbuda</div><div class="abs card-photo" role="img" aria-label="Palm trees and umbrellas on a sunny beach" style="background:linear-gradient(180deg,#2f7fd4,#3fb7d9 50%,#f2e4c2)"></div><div class="abs tag">FOR SALE</div><div class="abs btn-dark">MORE DETAILS</div></article>
<article class="abs card" style="left:88px;top:1216px"><div class="abs card-name">St. Kitts &amp; Nevis</div><div class="abs card-photo" role="img" aria-label="Rainforest river pool" style="background:linear-gradient(180deg,#2f4a2c,#5d7d3f 50%,#587a6a)"></div><div class="abs tag">FOR SALE</div><div class="abs btn-dark">MORE DETAILS</div></article>
<article class="abs card" style="left:434px;top:1216px"><div class="abs card-name">Jamaica</div><div class="abs card-photo" role="img" aria-label="Family looking over a tropical bay" style="background:linear-gradient(135deg,#e8c27a,#3aa7b8 55%,#2f6d3c)"></div><div class="abs tag">FOR SALE</div><div class="abs btn-dark">MORE DETAILS</div></article>
<article class="abs card" style="left:780px;top:1216px"><div class="abs card-name">St. Martin</div><div class="abs card-photo" role="img" aria-label="Tall palm trees along a beach" style="background:linear-gradient(180deg,#5fa3e0,#9fcbe8 55%,#e8dcc0)"></div><div class="abs tag">FOR SALE</div><div class="abs btn-dark">MORE DETAILS</div></article>

<section class="abs about">
  <h2 class="abs heading about-title">About plotVista</h2>
  <div class="abs about-rule"></div>
  <p class="abs about-text">Lorem Ipsum is simply dummy text of the printing and typesetting industry. Lorem Ipsum has been the industry's standard dummy text ever since the 1500s, when an unknown printer took a galley of type and scrambled it to make a type specimen book. It has survived not only five centuries, but also the leap into electronic typesetting, remaining essentially unchanged. It was popularised in the 1960s with the release of transfer sheets containing Lorem Ipsum passages, and more recently with desktop layout software including versions of Lorem Ipsum.</p>
  <div class="abs btn-blue" style="left:83px;top:278px;width:119px;height:45px">Read More</div>
  <div class="abs about-photo" role="img" aria-label="Smiling agent in a dark business suit"></div>
</section>

<h2 class="abs heading section-title" style="top:2145px">Join Our Team</h2>
<div class="abs rule" style="top:2192px;width:80px;left:560px"></div>

<div class="abs quote" style="left:88px;top:2288px;width:261px;height:143px;background:#c3c4c8;font-size:10px;line-height:15px">Our agents help local owners list plots quickly and reach serious buyers across every island, with honest guidance and fair fees at each step of the way.
  <div class="abs quote-icon"><svg width="16" height="12"><path d="M1 11V6l3-5h2L4 6h3v5zM9 11V6l3-5h2l-2 5h3v5z" fill="#c3c4c8"/></svg></div></div>
<div class="abs quote" style="left:428px;top:2257px;width:332px;height:179px;background:var(--purple);font-size:13px;line-height:20px">Lorem Ipsum is simply dummy text of the printing and typesetting industry. Lorem Ipsum has been the industry's standard dummy text ever since the 1500s, when an unknown printer took a galley of type and scrambled it to make a type specimen book....
  <div class="abs quote-icon" style="width:40px;height:40px;top:-20px;left:16px"><svg width="18" height="14"><path d="M1 13V7l3-6h2L4 7h3v6zM10 13V7l3-6h2l-2 6h3v6z" fill="#b768aa"/></svg></div></div>
<div class="abs quote" style="left:851px;top:2288px;width:261px;height:143px;background:#c3c4c8;font-size:10px;line-height:15px">Working with the team means flexible hours, strong support and a growing list of island lots, so every new member can build a steady client base.
  <div class="abs quote-icon"><svg width="16" height="12"><path d="M1 11V6l3-5h2L4 6h3v5zM9 11V6l3-5h2l-2 6h3v5z" fill="#c3c4c8"/></svg></div></div>

<div class="abs avatar" role="img" aria-label="Portrait of team member" style="left:176px;top:2450px;width:82px;height:82px"></div>
<div class="abs avatar" role="img" aria-label="Portrait of team member" style="left:540px;top:2459px;width:106px;height:106px"></div>
<div class="abs avatar" role="img" aria-label="Portrait of team member" style="left:940px;top:2450px;width:82px;height:82px"></div>
<div class="abs member" style="left:117px;top:2552px;width:200px">Remy Alston</div>
<div class="abs member" style="left:468px;top:2589px;width:250px;font-size:15px;color:var(--purple)">Carla M. Ocho Rios</div>
<div class="abs member" style="left:881px;top:2552px;width:200px">Dana P. Nassau, BS</div>

<section class="abs services">
  <h2 class="abs heading section-title" style="top:52px">Service Links</h2>
  <div class="abs rule" style="top:99px;width:80px;left:560px;background:var(--white)"></div>
  <div class="abs svc-label" style="left:88px">Developers</div>
  <div class="abs svc-label" style="left:296px">Surveyors</div>
  <div class="abs svc-label" style="left:504px">Appraisers</div>
  <div class="abs svc-label" style="left:712px">Landscapers</div>
  <div class="abs svc-label" style="left:920px">Financiers</div>
  <div class="abs svc-photo" role="img" aria-label="Developers reviewing plans" style="left:88px;background:linear-gradient(180deg,#8da0b4,#2f3540 60%,#d9dde0)"></div>
  <div class="abs svc-photo" role="img" aria-label="Surveyor with equipment in a field" style="left:296px;background:linear-gradient(180deg,#c8d6e2,#d9b34a 45%,#7d6a48)"></div>
  <div class="abs svc-photo" role="img" aria-label="Appraisers at a laptop" style="left:504px;background:linear-gradient(180deg,#f2f2f2,#c9c9c9 50%,#555c66)"></div>
  <div class="abs svc-photo" role="img" aria-label="Landscaper outdoors" style="left:712px;background:linear-gradient(180deg,#c8b07a,#6e7b4c 50%,#4a4d46)"></div>
  <div class="abs svc-photo" role="img" aria-label="Financier in a suit" style="left:920px;background:linear-gradient(180deg,#e6eaee,#3b4d78 55%,#1e2436)"></div>
  <div class="abs dot" style="left:572px"></div>
  <div class="abs dot" style="left:594px;background:var(--purple)"></div>
  <div class="abs dot" style="left:616px"></div>
</section>

<section class="abs signup">
  <div class="abs signup-title">SIGN UP TODAY</div>
  <div class="abs signup-sub">Sign up to receive timely, useful information in your inbox.</div>
  <div class="abs email">EMAIL</div>
  <div class="abs btn-blue submit">SUBMIT</div>
</section>

<footer class="abs footer">
  <div class="abs brand foot-brand" style="top:92px"><span class="mark" style="width:40px;height:40px;background:var(--white)"></span>PLOTVISTA</div>
  <div class="abs reach">TO REACH US:</div>
  <div class="abs contact" style="left:542px"><svg width="10" height="14"><path d="M5 1a4 4 0 0 1 4 4c0 3-4 8-4 8S1 8 1 5a4 4 0 0 1 4-4z" fill="#fff"/></svg>14 Harbour View Road, Bridgetown</div>
  <div class="abs contact" style="left:818px"><svg width="12" height="12"><path d="M2 1h3l1 3-2 1a7 7 0 0 0 3 3l1-2 3 1v3c-6 0-9-4-9-9z" fill="#fff"/></svg>555-0142-77</div>
  <div class="abs contact" style="left:958px"><svg width="14" height="10"><rect x="0.5" y="0.5" width="13" height="9" fill="#fff"/><path d="M1 1l6 5 6-5" stroke="#2a2d35" fill="none"/></svg>hello@plotvista.test</div>
  <div class="abs social" style="left:542px"></div>
  <div class="abs social" style="left:568px"></div>
  <div class="abs social" style="left:594px"></div>
  <div class="abs social" style="left:620px"></div>
  <div class="abs social" style="left:646px"></div>
  <div class="abs foot-line"></div>
  <div class="abs foot-links">Home &nbsp;|&nbsp; Buy &nbsp;|&nbsp; Sell &nbsp;|&nbsp; Services &nbsp;|&nbsp; Deals &nbsp;|&nbsp; Agents &nbsp;|&nbsp; Contact Us</div>
  <div class="abs copy">Copyright © 2017 plotVista.</div>
</footer>

</body>
</html>
```